Graphics for Verdaxa telehealth weight loss plans

Verdaxa focuses on delivering medical weight-loss using prescription medicine and telehealth consults. Verdaxa needs graphics for its ecommerce site for three weight loss plans. The plans are posted here with current graphics and descriptions of what is included with each plan. Please do not feel constrained by current graphics or styling.

- https://store.verdaxahealth.com/products/radiant-horizon-plan
- https://store.verdaxahealth.com/products/medication-kickstart-plan
- https://store.verdaxahealth.com/products/balanced-ascent-plan

The graphics need to look good on mobile and desktop browsers.

```html
<!DOCTYPE html>
<html lang="en">
<head>
<meta charset="utf-8">
<title>Verdaxa weight loss plans</title>
<link rel="stylesheet" href="https://fonts.googleapis.com/css2?family=Oswald:wght@300;400;500;600;700&display=swap">
<style>
  :root{
    --navy:#252460;
    --sky:#62d4f7;
    --cyan:#0bd3f2;
    --blue:#3b79c3;
    --white:#ffffff;
    --panel:#e6e7e9;
    --photo-a:#d9d9d9;
    --photo-b:#6f6f6f;
  }
  *{box-sizing:border-box;margin:0;padding:0}
  html,body{width:1200px;height:777px;overflow:hidden;background:var(--white)}
  body{position:relative;font-family:"Oswald",sans-serif;color:var(--navy)}
  .icons{position:absolute;width:0;height:0}

  .plan{position:absolute;top:12px;width:381px;height:492px;background:var(--card-bg);color:var(--card-ink);overflow:hidden}
  .plan--kickstart{left:17px;--card-bg:var(--sky);--card-ink:var(--navy);--band-bg:var(--navy);--band-ink:var(--white);--dot-bg:var(--navy);--dot-ink:var(--white);--rule:var(--navy)}
  .plan--ascent{left:410px;--card-bg:var(--navy);--card-ink:var(--cyan);--band-bg:var(--cyan);--band-ink:var(--navy);--dot-bg:var(--cyan);--dot-ink:var(--navy);--rule:var(--cyan)}
  .plan--horizon{left:802px;--card-bg:var(--blue);--card-ink:var(--white);--band-bg:var(--white);--band-ink:var(--navy);--dot-bg:var(--white);--dot-ink:var(--navy);--rule:var(--white)}

  .plan__photo{position:absolute;left:0;top:0;width:100%;height:158px;background:linear-gradient(120deg,var(--photo-a),var(--photo-b) 55%,#bdbdbd)}
  .plan__band{position:absolute;left:0;top:112px;width:250px;height:45px;background:var(--band-bg)}
  .plan__name{position:absolute;left:27px;top:112px;font-weight:700;font-size:37px;line-height:45px;letter-spacing:.2px;color:var(--band-ink);white-space:nowrap}
  .plan__name-rest{position:absolute;left:27px;top:158px;font-weight:700;font-size:37px;line-height:45px;color:var(--title-rest,var(--card-ink))}
  .plan--ascent .plan__name-rest,.plan--horizon .plan__name-rest{--title-rest:var(--white)}
  .plan--kickstart .plan__name-rest{--title-rest:var(--navy)}
  .plan__kind{position:absolute;left:27px;top:204px;font-size:16px;font-weight:400;line-height:20px;white-space:nowrap}
  .plan__includes{position:absolute;left:27px;top:232px;width:325px;font-size:14.5px;font-weight:500;line-height:20px;padding-bottom:4px;border-bottom:1px solid var(--rule)}
  .plan--ascent .plan__kind{display:none}

  .feature{position:absolute;display:flex;align-items:center;gap:6px;font-size:13.5px;font-weight:500;line-height:15px;white-space:nowrap}
  .feature small{font-size:10px;font-weight:400}
  .dot{flex:none;width:46px;height:46px;border-radius:50%;background:var(--dot-bg);color:var(--dot-ink);display:flex;align-items:center;justify-content:center}
  .dot svg{width:30px;height:30px}
  .dot--pills{flex-direction:column;gap:0}
  .dot--pills b{font-size:9.5px;font-weight:500;line-height:11px}
  .dot--pills svg{width:18px;height:12px}

  .paygo{position:absolute;display:flex;align-items:center;height:48px}
  .paygo .dot{width:48px;height:48px;position:relative;z-index:1}
  .paygo__bar{height:20px;margin-left:-6px;padding:0 14px 0 13px;background:var(--dot-bg);color:var(--dot-ink);font-size:12.5px;font-weight:500;line-height:20px;white-space:nowrap}
  .plan__note{position:absolute;left:32px;top:465px;font-size:12px;font-weight:300;color:var(--cyan)}

  .legend{position:absolute;left:109px;top:544px;width:981px;height:201px;background:var(--panel);--dot-bg:var(--navy);--dot-ink:var(--white)}
  .legend__tab{position:absolute;left:135px;top:531px;width:110px;height:26px;background:var(--navy);color:var(--white);font-size:17px;font-weight:500;line-height:26px;text-align:center}
  .legend .feature{font-size:18.5px;line-height:20px;gap:7px}
  .legend .feature small{font-size:13px}
  .legend .dot{width:60px;height:60px}
  .legend .dot svg{width:38px;height:38px}
  .legend .dot--pills b{font-size:12.5px;line-height:14px}
  .legend .dot--pills svg{width:24px;height:16px}
  .legend .paygo{height:64px}
  .legend .paygo .dot{width:64px;height:64px}
  .legend .paygo__bar{height:26px;line-height:26px;font-size:18.5px;padding:0 20px 0 14px;width:301px}
</style>
</head>
<body>

<svg class="icons" aria-hidden="true">
  <defs>
    <symbol id="i-online" viewBox="0 0 40 40" fill="none" stroke="currentColor" stroke-width="1.6" stroke-linejoin="round" stroke-linecap="round">
      <rect x="7" y="15" width="22" height="14" rx="1"/>
      <path d="M4 31h28M15 27c0-3 2-4 3-4s3 1 3 4"/>
      <circle cx="18" cy="20" r="2"/>
      <path d="M23 7h13v10h-5l-3 3v-3h-5z"/>
      <path d="M26 10h7M26 12.5h7M26 15h4"/>
    </symbol>
    <symbol id="i-door" viewBox="0 0 40 40" fill="none" stroke="currentColor" stroke-width="1.6" stroke-linejoin="round">
      <path d="M12 34V6h15v28M9 34h22"/>
      <circle cx="15" cy="12" r=".8" fill="currentColor"/>
      <rect x="19" y="25" width="10" height="9"/>
      <path d="M22 29h4M24 25v3"/>
    </symbol>
    <symbol id="i-rx" viewBox="0 0 40 40" fill="none" stroke="currentColor" stroke-width="1.6" stroke-linejoin="round" stroke-linecap="round">
      <path d="M10 5h14l6 6v10M30 28v6H10V5"/>
      <path d="M24 5v6h6M14 16h12M14 20h12M14 24h8M14 28h6"/>
      <path d="M14 8v5M14 8h2.5a1.5 1.5 0 010 3H14M16 11l3 3"/>
      <rect x="23" y="24" width="12" height="6" rx="3" transform="rotate(-40 29 27)"/>
      <path d="M27 29l4-4"/>
    </symbol>
    <symbol id="i-capsules" viewBox="0 0 30 20" fill="none" stroke="currentColor" stroke-width="2.2">
      <rect x="2" y="6" width="16" height="8" rx="4" transform="rotate(-35 10 10)"/>
      <rect x="12" y="6" width="16" height="8" rx="4" transform="rotate(-35 20 10)"/>
    </symbol>
    <symbol id="i-doctor" viewBox="0 0 40 40" fill="none" stroke="currentColor" stroke-width="1.6" stroke-linecap="round" stroke-linejoin="round">
      <path d="M8 35c0-7 5-11 12-11s12 4 12 11"/>
      <path d="M14 25v5a3 3 0 006 0M26 25v4"/>
      <circle cx="26" cy="31" r="2"/>
      <path d="M13 14c0-5 3-8 7-8s7 3 7 8-3 8-7 8-7-3-7-8z"/>
    </symbol>
    <symbol id="i-clipboard" viewBox="0 0 40 40" fill="none" stroke="currentColor" stroke-width="1.6" stroke-linecap="round" stroke-linejoin="round">
      <path d="M15 7h-5v28h14M25 7h5v12"/>
      <rect x="15" y="5" width="10" height="4" rx="1"/>
      <path d="M13 14l1.5 1.5 2.5-3M19 14h7M13 20l1.5 1.5 2.5-3M19 20h7M13 26l1.5 1.5 2.5-3M19 26h4"/>
      <path d="M30 23c-3-2-6 0-6 4s2 7 4 7c1 0 1-.5 2-.5s1 .5 2 .5c2 0 4-3 4-7s-3-6-6-4zM30 23c0-2 1-3 2-3"/>
    </symbol>
    <symbol id="i-coach" viewBox="0 0 40 40" fill="none" stroke="currentColor" stroke-width="1.6" stroke-linecap="round" stroke-linejoin="round">
      <path d="M20 12c-6-4-14 0-13 9s6 12 10 12c1.5 0 2-.6 3-.6s1.5.6 3 .6c4 0 9-3 10-12s-7-13-13-9z"/>
      <path d="M20 12c0-3 2-5 4-6M18 10c-1-2-3-3-5-3 0 2 2 3 5 3"/>
      <path d="M8 20h24M8 25h24M12 20v2.5M15 20v2.5M18 20v2.5M21 20v2.5M24 20v2.5M27 20v2.5"/>
    </symbol>
    <symbol id="i-plan" viewBox="0 0 40 40" fill="none" stroke="currentColor" stroke-width="1.6" stroke-linecap="round" stroke-linejoin="round">
      <path d="M6 35V22c0-3 3-5 7-5s7 2 7 5v5"/>
      <path d="M9 8h8v6H9zM11 27v4h4"/>
      <circle cx="28" cy="28" r="8"/>
      <path d="M23 28h10M24 30.5h8M25 26c1-2 5-2 6 0"/>
    </symbol>
    <symbol id="i-pay" viewBox="0 0 40 40" fill="none" stroke="currentColor" stroke-width="1.6" stroke-linecap="round" stroke-linejoin="round">
      <ellipse cx="21" cy="13" rx="13" ry="6"/>
      <path d="M8 13v5c0 3.3 5.8 6 13 6s13-2.7 13-6v-5"/>
      <path d="M17 10l8 6M15 13h12M18 9.5v7M24 9.5v7"/>
      <path d="M8 22c-1 7 7 12 16 11l4-.5"/>
      <path d="M25 29l4 3.5-4 3"/>
    </symbol>
  </defs>
</svg>

<!-- Medication Kickstart Plan -->
<section class="plan plan--kickstart">
  <div class="plan__photo" role="img" aria-label="Black and white photo of a measuring tape around a waist with capsules"></div>
  <div class="plan__band"></div>
  <h2 class="plan__name">MEDICATION</h2>
  <p class="plan__name-rest">KICKSTART PLAN</p>
  <p class="plan__kind">PHYSICIAN CONSULTATION PHENTERMINE PROGRAM</p>
  <h3 class="plan__includes">Includes</h3>

  <div class="feature" style="left:26px;top:265px"><span class="dot"><svg><use href="#i-online"/></svg></span>100% online.</div>
  <div class="feature" style="left:154px;top:265px"><span class="dot"><svg><use href="#i-door"/></svg></span><span>Real Phentermine <small>(37.5mg/Pill)</small><br>delivered to your door</span></div>
  <div class="feature" style="left:26px;top:317px"><span class="dot"><svg><use href="#i-rx"/></svg></span><span>Phentermine<br>prescription</span></div>
  <div class="feature" style="left:154px;top:317px"><span class="dot dot--pills"><b>30 pills</b><svg><use href="#i-capsules"/></svg></span>1 month supply</div>
  <div class="feature" style="left:26px;top:370px"><span class="dot"><svg><use href="#i-doctor"/></svg></span><span>Medical<br>consultation</span></div>
  <div class="feature" style="left:154px;top:370px"><span class="dot"><svg><use href="#i-clipboard"/></svg></span><span>FREE Introductory Nutritionist<br>consult on your first month</span></div>

  <div class="paygo" style="left:26px;top:423px"><span class="dot"><svg><use href="#i-pay"/></svg></span><span class="paygo__bar">Month-to-month pay as you go</span></div>
</section>

<!-- Balanced Ascent Plan -->
<section class="plan plan--ascent">
  <div class="plan__photo" role="img" aria-label="Black and white photo of a woman in sportswear holding a shaker bottle"></div>
  <div class="plan__band"></div>
  <h2 class="plan__name">BALANCED</h2>
  <p class="plan__name-rest">ASCENT PLAN</p>
  <h3 class="plan__includes" style="top:228px">Includes</h3>

  <div class="feature" style="left:24px;top:266px"><span class="dot"><svg><use href="#i-online"/></svg></span>100% online.</div>
  <div class="feature" style="left:185px;top:266px"><span class="dot"><svg><use href="#i-clipboard"/></svg></span>Expert nutrition consult</div>
  <div class="feature" style="left:22px;top:322px"><span class="dot" style="width:48px;height:48px"><svg><use href="#i-plan"/></svg></span><span>Custom crafted<br>diet plan to achieve<br>your goals</span></div>
  <div class="feature" style="left:185px;top:322px"><span class="dot"><svg><use href="#i-coach"/></svg></span><span>Nutrition coaching<br>to improve your health<br>and vitality</span></div>

  <div class="paygo" style="left:22px;top:381px"><span class="dot"><svg><use href="#i-pay"/></svg></span><span class="paygo__bar">Month-to-month pay as you go</span></div>
  <p class="plan__note">*Does not include medication</p>
</section>

<!-- Radiant Horizon Plan -->
<section class="plan plan--horizon">
  <div class="plan__photo" role="img" aria-label="Black and white photo of a toned male torso with capsules"></div>
  <div class="plan__band"></div>
  <h2 class="plan__name">RADIANT</h2>
  <p class="plan__name-rest" style="top:154px;font-size:35px">HORIZON PLAN</p>
  <p class="plan__kind">PHYSICIAN CONSULTATION PHENTERMINE PROGRAM</p>
  <h3 class="plan__includes">Includes</h3>

  <div class="feature" style="left:20px;top:265px"><span class="dot"><svg><use href="#i-online"/></svg></span>100% online.</div>
  <div class="feature" style="left:169px;top:265px"><span class="dot"><svg><use href="#i-door"/></svg></span><span>Real Phentermine <small>(37.5mg/pill)</small><br>delivered to your door</span></div>
  <div class="feature" style="left:20px;top:317px"><span class="dot"><svg><use href="#i-rx"/></svg></span><span>Phentermine<br>prescription</span></div>
  <div class="feature" style="left:169px;top:317px"><span class="dot dot--pills"><b>30 pills</b><svg><use href="#i-capsules"/></svg></span>1 month supply</div>
  <div class="feature" style="left:20px;top:371px"><span class="dot"><svg><use href="#i-plan"/></svg></span><span>Custom crafted<br>diet plan to achieve<br>your goals</span></div>
  <div class="feature" style="left:169px;top:371px"><span class="dot"><svg><use href="#i-coach"/></svg></span><span>Nutrition coaching<br>to improve your health<br>and vitality</span></div>

  <div class="paygo" style="left:20px;top:423px"><span class="dot"><svg><use href="#i-pay"/></svg></span><span class="paygo__bar">Month-to-month pay as you go</span></div>
</section>

<!-- Pictogram legend -->
<section class="legend">
  <div class="feature" style="left:26px;top:37px"><span class="dot"><svg><use href="#i-online"/></svg></span>100% online.</div>
  <div class="feature" style="left:196px;top:37px"><span class="dot"><svg><use href="#i-door"/></svg></span><span>Real Phentermine <small>(37.5mg/Pill)</small><br>delivered to your door</span></div>
  <div class="feature" style="left:479px;top:37px"><span class="dot"><svg><use href="#i-rx"/></svg></span><span>Phentermine<br>prescription</span></div>
  <div class="paygo" style="left:661px;top:35px"><span class="dot"><svg><use href="#i-pay"/></svg></span><span class="paygo__bar">Month-to-month pay as you go</span></div>

  <div class="feature" style="left:26px;top:112px"><span class="dot"><svg><use href="#i-doctor"/></svg></span><span>Medical<br>consultation</span></div>
  <div class="feature" style="left:195px;top:112px"><span class="dot"><svg><use href="#i-clipboard"/></svg></span><span>FREE Introductory Nutritionist<br>consult on your first month</span></div>
  <div class="feature" style="left:480px;top:112px"><span class="dot"><svg><use href="#i-coach"/></svg></span><span>Nutrition coaching<br>to improve your health<br>and vitality</span></div>
  <div class="feature" style="left:732px;top:112px"><span class="dot dot--pills"><b>30 pills</b><svg><use href="#i-capsules"/></svg></span>1 month supply</div>
</section>
<div class="legend__tab">Pictograms</div>

</body>
</html>
```